Brochure Design Project

We need a brochure for our acting school, website is
www.stagelarkhouse.com - It needs to reflect youth, vitality, and people's DREAMS coming true...colors should be red and black, but open to something new as well...the courses included should be
Players' Rapid Forge, Steady Stage Bundle, And The Mastery Track

Emphasis on Players' Rapid Forge is the short term intensity.
Steady Stage Bundle is the benefit of getting all the tools to look for acting work.
Mastery Track is becoming a pro, and if you are in another country, being provided with a visa to come to the U.S.

I have attached pictures and logos...I will submit the copy once there is a framework...the OLD brochure is attached as well...

Thank you...

Marlon

Reason: We would like to see a couple more ideas...

Reason: HI there designers! Thanks for your submissions. We are almost ready to pick a design. Thanks for the understanding.

Target Market(s)

18-35 year olds...fairly affluent, educated, American, European, or Australian

Industry/Entity Type

School

Requirements
Must have
• Make it fun, clean, clear, and NOT corporate.

```html
<!DOCTYPE html>
<html lang="en">
<head>
<meta charset="utf-8">
<title>Stagelark House – Programs Brochure</title>
<link rel="stylesheet" href="https://fonts.googleapis.com/css2?family=Anton&family=Oswald:wght@500;700&family=Open+Sans:wght@400;600&display=swap">
<style>
  :root{
    --page:#eeeff1;
    --paper:#e2e3e6;
    --paper-light:#f3f4f6;
    --navy:#27405f;
    --navy-deep:#1b2e46;
    --ink:#141414;
    --pink:#e4157c;
    --ring:#1f5fa3;
    --body-dark:#3a3d42;
    --body-light:#e8edf3;
  }
  *{box-sizing:border-box;margin:0;padding:0}
  html,body{width:1200px;height:862px;overflow:hidden}
  body{background:var(--page);font-family:"Open Sans",Arial,sans-serif;position:relative}

  .brochure-inside{position:absolute;left:40px;top:121px;width:780px;height:620px;display:flex;box-shadow:0 8px 24px rgba(0,0,0,.18)}
  .panel{position:relative;width:260px;height:620px;overflow:hidden}
  .panel + .panel{border-left:1px solid rgba(0,0,0,.12)}

  /* shared type */
  .program-heading{position:absolute;left:0;display:flex;align-items:center;height:26px;padding:0 12px;background:var(--navy-deep);color:#fff;font-family:"Oswald",Arial,sans-serif;font-weight:700;font-size:13px;letter-spacing:.4px;text-transform:uppercase}
  .duration{position:absolute;background:var(--pink);color:#fff;font-family:"Oswald",Arial,sans-serif;font-weight:500;font-size:7.5px;letter-spacing:.8px;padding:1px 6px;text-transform:uppercase}
  .copy{position:absolute;left:16px;right:16px;font-size:6.6px;line-height:1.55;text-align:justify}
  .copy p + p{margin-top:5px}
  .copy-light{color:var(--body-light)}
  .copy-dark{color:var(--body-dark)}
  .photo{position:absolute;left:16px;right:16px;border:3px solid #fff}

  /* panel 1 */
  .panel-programs{background:linear-gradient(160deg,var(--paper-light) 0%,var(--paper) 55%,#cfd1d5 100%)}
  .title-block{position:absolute;left:0;top:36px;width:210px;height:118px;background:var(--ink);clip-path:polygon(0 6%,100% 0,94% 100%,0 100%)}
  .title-block h1{position:absolute;left:16px;top:10px;color:#fff;font-family:"Anton",Impact,sans-serif;font-weight:400;font-size:31px;line-height:.98;text-transform:uppercase}
  .tag-programs{position:absolute;left:104px;top:146px;background:var(--pink);color:#fff;font-family:"Oswald",Arial,sans-serif;font-size:8px;letter-spacing:1.5px;padding:2px 10px;text-transform:uppercase}
  .navy-block{position:absolute;left:0;top:170px;width:260px;height:250px;background:var(--navy);clip-path:polygon(0 4%,100% 0,100% 92%,0 100%)}
  .panel-programs .program-heading{width:228px}

  /* panel 2 */
  .panel-bundle{background:linear-gradient(175deg,#34506f 0%,var(--navy) 40%,var(--navy-deep) 100%)}
  .panel-bundle .program-heading{width:240px}

  /* panel 3 */
  .panel-mastery{background:linear-gradient(170deg,#dfe1e4 0%,#dfe1e4 4%,var(--navy) 4.1%,var(--navy-deep) 100%)}
  .panel-mastery .program-heading{width:220px}
  .closing-band{position:absolute;left:0;bottom:0;width:260px;height:86px;background:linear-gradient(160deg,#f4f5f7,#cfd2d6)}
  .closing-line{position:absolute;left:110px;bottom:26px;display:flex;flex-direction:column;align-items:flex-start}
  .closing-line .lead{background:var(--pink);color:#fff;font-family:"Oswald",Arial,sans-serif;font-weight:700;font-size:10px;padding:1px 6px;text-transform:uppercase}
  .closing-line .ask{background:var(--ink);color:#fff;font-family:"Anton",Impact,sans-serif;font-size:26px;line-height:1.1;padding:0 10px;text-transform:uppercase}

  /* cover */
  .brochure-cover{position:absolute;left:880px;top:121px;width:260px;height:620px;overflow:hidden;background:linear-gradient(165deg,#f6f7f8,#d4d6da);box-shadow:0 8px 24px rgba(0,0,0,.18)}
  .school-name{position:absolute;left:0;right:0;top:34px;display:flex;align-items:center;justify-content:center;gap:8px;font-family:"Oswald",Arial,sans-serif;font-weight:700;font-size:22px;letter-spacing:2px;color:#5b5e63;text-transform:uppercase}
  .school-name .dot{width:8px;height:8px;border-radius:50%;background:#5b5e63}
  .cover-photo{position:absolute;left:0;top:96px;width:260px;height:524px;background:
      radial-gradient(circle at 70% 8%,rgba(255,255,255,.55),transparent 18%),
      radial-gradient(circle at 40% 45%,rgba(170,120,100,.45),transparent 55%),
      linear-gradient(180deg,#1a1c22 0%,#2d2a2b 55%,#4a3528 85%,#6a4a30 100%);
      clip-path:polygon(0 3%,100% 0,100% 100%,0 100%)}
  .play-button{position:absolute;left:72px;top:266px;width:116px;height:116px}
  .cover-tagline{position:absolute;right:0;top:494px;display:flex;flex-direction:column;align-items:flex-end}
  .cover-tagline .program{background:var(--ink);color:#fff;font-family:"Oswald",Arial,sans-serif;font-weight:700;font-size:13px;line-height:1.15;padding:5px 12px 4px;text-transform:uppercase;text-align:left;width:130px}
  .cover-tagline .motto{background:var(--pink);color:#fff;font-size:10px;line-height:1.2;padding:3px 12px 5px;width:130px}
</style>
</head>
<body>

<main class="brochure-inside">

  <section class="panel panel-programs">
    <div class="title-block"><h1>What<br>We Do<br>About It</h1></div>
    <span class="tag-programs">• Programs •</span>
    <div class="navy-block"></div>

    <h2 class="program-heading" style="top:186px">Players' Rapid Forge I</h2>
    <span class="duration" style="left:190px;top:214px">4 Weeks</span>
    <div class="copy copy-light" style="top:236px">
      <p>Players' Rapid Forge I, created by Artistic Director Marlon Vesca, with over 1,200 graduates on ScreenLedger, offers an alternative to acting teacher worship: full time, 30 minutes on your feet, daily actors' training. We acknowledge the 21st century by offering only the practical and useful elements of the Resonant Technique and the Gesture Technique, as well as the practical application of all this to cold reading and scene study.</p>
      <p>Players' Rapid Forge I is four weeks of daily classes, by the end of which you will know if acting is your life's work or just a passing fancy.</p>
    </div>

    <h2 class="program-heading" style="top:436px">Players' Rapid Forge II</h2>
    <span class="duration" style="left:190px;top:464px">8 Weeks</span>
    <div class="copy copy-dark" style="top:484px">
      <p>The Army's Boot Camp prepares you for war. Players' Rapid Forge II prepares you for a much tougher battle – Show Business; that's why it's eight glorious weeks of daily work. Because after Rapid Forge II, you will never again be able to return to civilian life; you are now an actor. Here you will continue to learn and apply only the relevant aspects of the Resonant Technique and the Gesture Technique, you will learn true on-camera skills so that you can work on any type of shoot, and you will learn and APPLY business tools that will get you going in your career.</p>
    </div>
  </section>

  <section class="panel panel-bundle">
    <h2 class="program-heading" style="top:30px">The Steady Stage Bundle</h2>
    <span class="duration" style="left:196px;top:58px">3 Months</span>
    <div class="copy copy-light" style="top:78px">
      <p>There are those who come to Hollywood, manage to get an audition, go in hoping for the best, and fail miserably. There is something to be said for being ready for that kind of room. You only get one shot at a relationship with a casting director, a director or a producer, so give yourself the best. The Steady Stage Bundle gives you Players' Rapid Forge I and II back to back, plus everything you need to book the job, including a personalized way to market yourself. It leaves you with NO EXCUSES. So what are you waiting for?</p>
    </div>
    <div class="photo" role="img" aria-label="Photo of actors rehearsing a scene in front of a film camera crew" style="top:196px;height:112px;background:radial-gradient(circle at 30% 40%,#6d5a52,transparent 60%),linear-gradient(180deg,#2a2c33,#14161b)"></div>

    <h2 class="program-heading" style="top:330px">The Advanced Program</h2>
    <span class="duration" style="left:196px;top:358px">Ongoing</span>
    <div class="copy copy-light" style="top:380px">
      <p>Only auditioning, committed actors are invited to the Advanced Program. Why? Because we want to offer the best support in getting you in shape and in front of agents, managers and casting directors. During on-going courses, you will gain a deep understanding of character and script analysis, as well as invaluable experience playing many different kinds of parts in all of the genres you might audition for in today's industry.</p>
    </div>
    <div class="photo" role="img" aria-label="Photo of students watching a performance in a dim studio" style="top:478px;height:112px;background:radial-gradient(circle at 60% 35%,#5e4e48,transparent 60%),linear-gradient(180deg,#24262c,#111216)"></div>
  </section>

  <section class="panel panel-mastery">
    <h2 class="program-heading" style="top:40px">Mastery Track</h2>
    <span class="duration" style="left:176px;top:68px">2 Years</span>
    <div class="copy copy-light" style="top:90px">
      <p>Designed for actors who come to Los Angeles and are committed to turning their dream into reality, the 2 year Mastery Track gets you working on your craft 22 hours a week, every week.</p>
      <p>Utilizing only the effective and updated elements of the Resonant and Gesture techniques, you will learn the working actor business and become a performer ready for any stage or set. You will be able to book on a professional level and build a career with real training and a personal brand that lets you walk confidently into the industry.</p>
      <p>At the end of the two years you will receive a Mastery Track certificate of completion, something to be proud of.</p>
      <p>If you are an international student, The Mastery Track can support your student visa. Contact Stagelark House and we will do our best to arrange for you to come.</p>
    </div>
    <div class="photo" role="img" aria-label="Photo of an actor performing on a lit stage" style="top:400px;height:118px;background:radial-gradient(circle at 45% 45%,#5a4a44,transparent 55%),linear-gradient(180deg,#1f2126,#101114)"></div>
    <div class="closing-band"></div>
    <div class="closing-line"><span class="lead">If not now…</span><span class="ask">When?</span></div>
  </section>

</main>

<aside class="brochure-cover">
  <div class="school-name"><span class="dot"></span>Stagelark House</div>
  <div class="cover-photo" role="img" aria-label="Photo of a crowd of young actors under stage lights above the school's lit entrance at night"></div>
  <svg class="play-button" viewBox="0 0 116 116" aria-hidden="true">
    <circle cx="58" cy="58" r="55" fill="#fff"/>
    <circle cx="58" cy="58" r="46" fill="none" stroke="var(--ring)" stroke-width="7"/>
    <circle cx="58" cy="58" r="41" fill="#f3f3f4"/>
    <polygon points="46,36 46,80 82,58" fill="var(--pink)"/>
  </svg>
  <div class="cover-tagline">
    <span class="program">Players'<br>Rapid Forge</span>
    <span class="motto">Act on your<br>dream</span>
  </div>
</aside>

</body>
</html>
```